Reach Crafters Unique Marketing Website Design

I am starting a new company that is a thought leader in the marketing consulting space. The company is called Reach Crafters. We intend to build a Wordpress site on the Astra Theme with the Spectra builder. Our goal is to become the leading voice that empowers high-ticket service business leaders to become Reach Crafters by equipping them with the cutting-edge frameworks and decision grade intelligence taught in leading business schools. What we are looking for is a website design that is clean and professional, making some use of white space well also being eye catching and distinctive in the consulting space. We will probably want to have a video on the homepage not in the hero section, but just below to explain the company and what we do. Our tagline is "Be found. Be chosen." I have attached a brand guide with some messaging, our typography choices, and our color system. The full site will have a primary nav that is four pages - About us, Services, Insights (essentially a blog), and Contact Us. The goal of this project is to develop an art direction that I can give to a designer to build loads of new pages.

Target Market(s)

Business owners (mostly male) from 30-60 years old, looking to fix their sales and marketing funnel.

Industry/Entity Type

Marketing consulting

Font styles to use
Sans Serif

Requirements
Must have
• A clean, professional design that builds trust with owners of high-ticket service businesses. We need a space for explainer video, and sections that tell prospects what we do. Would also like to have a blog carousel.
Nice to have
• Social feeds, if possible. See attached documents for colors and fonts.
Should not have
• Our feel is professional enough to be trustworthy, but unique enough to be memorable. Cartoon ideas do not meet the professional test, and we do not want the website to appear feminine.

```html
<!DOCTYPE html>
<html lang="en">
<head>
<meta charset="utf-8">
<title>Reach Crafters — Be Found. Be Chosen.</title>
<link rel="stylesheet" href="https://fonts.googleapis.com/css2?family=Oswald:wght@400;500&family=Montserrat:ital,wght@0,400;0,500;0,600;0,700;1,400&display=swap">
<style>
:root{
  --blue:#2433f5;
  --navy:#0a1427;
  --navy-card:#111c33;
  --charcoal:#232323;
  --white:#ffffff;
  --ink:#1b1b1b;
  --muted:#5d5d5d;
  --green:#1fae5b;
  --soft:#cfd4e0;
}
*{margin:0;padding:0;box-sizing:border-box}
html,body{width:1200px;height:4392px;overflow:hidden}
body{font-family:"Montserrat",sans-serif;color:var(--white);background:var(--charcoal)}
section,header,footer{position:relative;width:1200px;overflow:hidden}
.abs{position:absolute}
.display{font-family:"Oswald",sans-serif;font-weight:400;text-transform:uppercase;letter-spacing:-.5px;line-height:1.15}
.btn{position:absolute;display:flex;align-items:center;justify-content:center;background:var(--blue);color:var(--white);font-weight:700;font-size:13px;text-transform:uppercase;letter-spacing:.3px;clip-path:polygon(0 0,100% 0,100% 100%,10px 100%,0 calc(100% - 10px))}
.btn.oswald{font-family:"Oswald",sans-serif;font-weight:500;font-size:18px;letter-spacing:0}

/* hero */
.hero{height:639px;background:radial-gradient(ellipse at 78% 35%,#1b4f96 0%,#0d2a55 30%,#07142b 62%,#050c1a 100%)}
.hero-art{inset:0}
.brand{left:150px;top:12px;font-family:"Oswald",sans-serif;font-size:40px;font-weight:400;color:var(--white);letter-spacing:-.5px}
.nav{left:579px;top:29px;display:flex;gap:32px;font-size:14px;font-weight:500}
.nav .active{color:#3a8bff}
.nav-cta{left:915px;top:22px;width:135px;height:43px}
.hero h1{left:150px;top:212px;font-size:56px;line-height:69px}
.hero p{left:152px;top:362px;width:500px;font-size:13.5px;line-height:23px;font-weight:500}
.hero .btn{left:152px;top:426px;width:187px;height:43px}

/* about */
.about{height:653px;background:var(--charcoal)}
.frame{left:150px;top:116px;width:186px;height:448px;border-left:4px solid var(--blue);border-bottom:4px solid var(--blue)}
.video{left:169px;top:80px;width:422px;height:464px;background:linear-gradient(135deg,#c9d3dc 0%,#8a9aa8 45%,#4b5866 100%);clip-path:polygon(0 0,100% 0,100% 84%,84% 100%,0 100%)}
.play{left:341px;top:271px}
.about .label{left:648px;top:100px;font-size:26px}
.about h2{left:648px;top:154px;font-size:44px;line-height:59px}
.about p{left:648px;top:290px;width:402px;font-size:12.5px;line-height:25px;text-align:justify}
.about .btn{left:649px;top:469px;width:152px;height:46px}

/* services */
.services{height:714px;background:var(--navy)}
.section-label{font-size:27px}
.section-title{font-size:44px}
.services .section-label{left:150px;top:76px}
.services .section-title{left:150px;top:122px}
.services .btn,.social .btn{left:868px;top:77px;width:182px;height:44px}
.cards{left:150px;top:208px;display:flex;gap:12px}
.card{width:219px;height:384px;background:var(--navy-card)}
.card.featured{background:var(--blue)}
.card-img{height:234px}
.card h3{margin:18px 16px 0;font-size:13.5px;font-weight:700;line-height:18px;text-transform:uppercase;min-height:36px}
.card p{margin:8px 18px 0;font-size:12.5px;line-height:22px;color:#d9def0}
.card.featured p{color:#e6e9ff}

/* insights */
.insights{height:846px;background:var(--white);color:var(--ink)}
.center{width:1200px;text-align:center;left:0}
.insights .section-label{top:114px}
.insights .section-title{top:160px}
.feature{left:153px;top:252px;width:425px;height:468px;background:linear-gradient(160deg,#b8c3cc 0%,#7c8893 50%,#3c434b 100%)}
.post{left:609px;display:flex;gap:20px;width:441px}
.thumb{width:155px;height:142px;flex:none}
.post-date{color:var(--green);font-size:13px;font-weight:600;margin-top:10px}
.post h4{font-size:16px;font-weight:600;margin:12px 0 8px}
.post p{font-size:11px;line-height:18px;color:var(--muted)}

/* testimonials */
.testimonials{height:579px;background:var(--charcoal)}
.testimonials .section-label{top:114px}
.testimonials .section-title{top:164px}
.quote{top:221px;width:263px;height:247px;background:var(--white);color:var(--ink);padding:16px 18px}
.avatar{width:64px;height:64px;border-radius:50%;border:3px solid var(--blue);background:linear-gradient(135deg,#8a7a68,#4c5560);float:left;margin-right:14px}
.quote h5{font-size:15px;font-weight:600;padding-top:13px;text-transform:uppercase}
.quote .date{font-size:11px;color:var(--muted);margin-top:4px}
.quote p{clear:both;padding-top:20px;font-size:11.5px;font-style:italic;line-height:21px;color:#444}
.arrow{top:334px}

/* social */
.social{height:535px;background:var(--navy)}
.social .section-label{left:150px;top:78px}
.social .section-title{left:150px;top:124px}
.tiles{left:150px;top:215px;display:flex;gap:12px}
.tile{width:216px;height:232px}
.tile.red{background:linear-gradient(135deg,#e8322f,#b8161a)}

/* footer */
.site-footer{height:426px;background:var(--charcoal);text-align:center}
.foot-brand{top:90px;font-family:"Oswald",sans-serif;font-size:54px;left:0;width:1200px}
.foot-nav{top:176px;left:0;width:1200px;display:flex;justify-content:center;gap:0;font-size:14px;font-weight:500}
.foot-nav span{padding:0 14px;border-left:1px solid var(--blue)}
.foot-nav span:first-child{border-left:none}
.rule{left:300px;width:600px;height:1px;background:#3a3a3a}
.contact{top:256px;display:flex;align-items:center;gap:14px;text-align:left;font-size:13px;font-weight:500;line-height:18px}
.contact-icon{width:38px;height:38px;background:var(--blue);border-radius:4px;display:flex;align-items:center;justify-content:center}
.copy{top:378px;left:0;width:1200px;font-size:13px;font-weight:500}
</style>
</head>
<body>

<header class="hero">
  <div class="abs hero-art" role="img" aria-label="Dark blue data landscape with glowing bar chart and rising arrow"></div>
  <div class="abs brand">REACH CRAFTERS</div>
  <nav class="abs nav"><span class="active">Home</span><span>About us</span><span>Services</span><span>Insights</span></nav>
  <a class="btn oswald nav-cta">CONTACT US</a>
  <h1 class="abs display">Become a Reach Crafter.<br>Be found. Be chosen.</h1>
  <p class="abs">We equip high-ticket service leaders with elite frameworks, decision-grade intelligence, and proven demand-generation systems.</p>
  <a class="btn oswald">EXPLORE SERVICES</a>
</header>

<section class="about">
  <div class="abs frame"></div>
  <div class="abs video" role="img" aria-label="Explainer video still: consultants reviewing reports at an office table"></div>
  <svg class="abs play" width="82" height="82" viewBox="0 0 82 82" aria-hidden="true"><circle cx="41" cy="41" r="41" fill="#2433f5"/><path d="M32 24 L60 41 L32 58 Z" fill="#fff"/></svg>
  <div class="abs display label">About us</div>
  <h2 class="abs display">What Reach Crafters does -<br>in 90 seconds</h2>
  <p class="abs">Lorem ipsum dolor sit amet, consectetur adipiscing elit, sed do eiusmod tempor incididunt ut labore et dolore magna aliqua. Ut enim ad minim veniam, quis nostrud exercitation ullamco laboris nisi ut aliquip ex ea commodo consequat. Duis aute irure dolor in reprehenderit in voluptate velit esse cillum dolore eu fugiat nulla pariatur.</p>
  <a class="btn">Read more</a>
</section>

<section class="services">
  <div class="abs display section-label">Our services</div>
  <h2 class="abs display section-title">How we help you win demand</h2>
  <a class="btn">View all services</a>
  <div class="abs cards">
    <article class="card featured">
      <div class="card-img" role="img" aria-label="Executive holding a glowing strategy diagram" style="background:linear-gradient(160deg,#1d2a44,#0c1830 60%,#1f4f9c)"></div>
      <h3>Demand strategy &amp; market positioning</h3>
      <p>Lorem ipsum dolor sit amet, consectetur adipiscing elit, sed do eiusmod tempor</p>
    </article>
    <article class="card">
      <div class="card-img" role="img" aria-label="Rising growth chart above a laptop" style="background:linear-gradient(160deg,#d9dde2,#7e8792 55%,#2b2f36)"></div>
      <h3>Revenue &amp; pipeline intelligence</h3>
      <p>Lorem ipsum dolor sit amet, consectetur adipiscing elit, sed do eiusmod tempor</p>
    </article>
    <article class="card">
      <div class="card-img" role="img" aria-label="Blue financial data graph" style="background:linear-gradient(180deg,#0a2a6b,#1a56c8 55%,#0b1c44)"></div>
      <h3>Go-to-market systems</h3>
      <p>Lorem ipsum dolor sit amet, consectetur adipiscing elit, sed do eiusmod tempor</p>
    </article>
    <article class="card">
      <div class="card-img" role="img" aria-label="Hand on laptop with digital planning overlay" style="background:linear-gradient(160deg,#e4e8ee,#a5b0bd 55%,#5d6977)"></div>
      <h3>Executive advisory &amp; growth planning</h3>
      <p>Lorem ipsum dolor sit amet, consectetur adipiscing elit, sed do eiusmod tempor</p>
    </article>
  </div>
</section>

<section class="insights">
  <div class="abs center display section-label">Insights</div>
  <h2 class="abs center display section-title">Insights for demand leaders</h2>
  <div class="abs feature" role="img" aria-label="Business team meeting around a laptop in a glass office"></div>
  <article class="abs post" style="top:252px">
    <div class="thumb" role="img" aria-label="Team working in a sunlit office" style="background:linear-gradient(150deg,#d8c7a8,#6e5a44 60%,#2e2620)"></div>
    <div><div class="post-date">Jan 27, 2025</div><h4>Strategic growth articles</h4><p>Lorem ipsum dolor sit amet, consectetur adipiscing elit, sed do eiusmod tempor incididunt ut labore et dolore</p></div>
  </article>
  <article class="abs post" style="top:416px">
    <div class="thumb" role="img" aria-label="Analyst with digital dashboard overlay" style="background:linear-gradient(150deg,#1b3660,#4a7fb8 55%,#c5d4e4)"></div>
    <div><div class="post-date">Jan 27, 2025</div><h4>Strategic growth articles</h4><p>Lorem ipsum dolor sit amet, consectetur adipiscing elit, sed do eiusmod tempor incididunt ut labore et dolore</p></div>
  </article>
  <article class="abs post" style="top:580px">
    <div class="thumb" role="img" aria-label="Printed charts on a desk" style="background:linear-gradient(150deg,#eef0f3,#a9b2bd 55%,#56606b)"></div>
    <div><div class="post-date">Jan 27, 2025</div><h4>Strategic growth articles</h4><p>Lorem ipsum dolor sit amet, consectetur adipiscing elit, sed do eiusmod tempor incididunt ut labore et dolore</p></div>
  </article>
</section>

<section class="testimonials">
  <div class="abs center display section-label">Testimonials</div>
  <h2 class="abs center display section-title">Trusted by growth-focused leaders</h2>
  <svg class="abs arrow" style="left:109px" width="20" height="20" viewBox="0 0 20 20" aria-hidden="true"><circle cx="10" cy="10" r="10" fill="#fff"/><path d="M11.5 5.5 L7 10 L11.5 14.5" stroke="#232323" stroke-width="2.4" fill="none"/></svg>
  <svg class="abs arrow" style="left:1073px" width="20" height="20" viewBox="0 0 20 20" aria-hidden="true"><circle cx="10" cy="10" r="10" fill="#fff"/><path d="M8.5 5.5 L13 10 L8.5 14.5" stroke="#232323" stroke-width="2.4" fill="none"/></svg>
  <article class="abs quote" style="left:153px">
    <div class="avatar" role="img" aria-label="Client portrait"></div>
    <h5>Marek Dalton</h5><div class="date">01 Oct 2025</div>
    <p>Sed ut perspiciatis unde omnis iste natus error sit voluptatem accusantium doloremque laudantium, totam rem aperiam, eaque ipsa quae ab illo inventore veritatis et quasi architecto beatae vitae dicta sunt explicabo.</p>
  </article>
  <article class="abs quote" style="left:470px">
    <div class="avatar" role="img" aria-label="Client portrait"></div>
    <h5>Marek Dalton</h5><div class="date">01 Oct 2025</div>
    <p>Sed ut perspiciatis unde omnis iste natus error sit voluptatem accusantium doloremque laudantium, totam rem aperiam, eaque ipsa quae ab illo inventore veritatis et quasi architecto beatae vitae dicta sunt explicabo.</p>
  </article>
  <article class="abs quote" style="left:787px">
    <div class="avatar" role="img" aria-label="Client portrait"></div>
    <h5>Marek Dalton</h5><div class="date">01 Oct 2025</div>
    <p>Sed ut perspiciatis unde omnis iste natus error sit voluptatem accusantium doloremque laudantium, totam rem aperiam, eaque ipsa quae ab illo inventore veritatis et quasi architecto beatae vitae dicta sunt explicabo.</p>
  </article>
</section>

<section class="social">
  <div class="abs display section-label">Social feed</div>
  <h2 class="abs display section-title">Follow Reach Crafters</h2>
  <a class="btn">View all social</a>
  <div class="abs tiles">
    <div class="tile red" role="img" aria-label="Social feed post in red"></div>
    <div class="tile" role="img" aria-label="Social post: professional portrait" style="background:linear-gradient(150deg,#c9a27a,#6b4f3a 55%,#2c4a6e)"></div>
    <div class="tile" role="img" aria-label="Social post: presenter at a whiteboard" style="background:linear-gradient(150deg,#f1f3f5,#c4cbd3 55%,#8a7560)"></div>
    <div class="tile" role="img" aria-label="Social post: speaker pointing at a screen" style="background:linear-gradient(150deg,#e7ecf1,#aab7c4 55%,#4c5a6a)"></div>
  </div>
</section>

<footer class="site-footer">
  <div class="abs foot-brand">REACH CRAFTERS</div>
  <nav class="abs foot-nav"><span>Home</span><span>About us</span><span>Services</span><span>Insights</span><span>Contact Us</span></nav>
  <div class="abs rule" style="top:236px"></div>
  <div class="abs contact" style="left:360px">
    <div class="contact-icon"><svg width="16" height="16" viewBox="0 0 24 24" aria-hidden="true"><path fill="#fff" d="M6.6 10.8c1.4 2.8 3.8 5.1 6.6 6.6l2.2-2.2c.3-.3.7-.4 1-.2 1.1.4 2.3.6 3.6.6.6 0 1 .4 1 1V20c0 .6-.4 1-1 1C10.6 21 3 13.4 3 4c0-.6.4-1 1-1h3.5c.6 0 1 .4 1 1 0 1.3.2 2.5.6 3.6.1.3 0 .7-.2 1z"/></svg></div>
    <div>Call:<br>+1 555-014-2200</div>
  </div>
  <div class="abs contact" style="left:644px">
    <div class="contact-icon"><svg width="16" height="16" viewBox="0 0 24 24" aria-hidden="true"><path fill="#fff" d="M3 5h18v14H3z"/><path d="M3 6l9 7 9-7" stroke="#2433f5" stroke-width="2" fill="none"/></svg></div>
    <div>Email:<br>info@reachcrafters.com</div>
  </div>
  <div class="abs rule" style="top:338px"></div>
  <div class="abs copy">© 2026 - REACH CRAFTERS. | All rights reserved</div>
</footer>

</body>
</html>
```